Custom unique Stationary design for Logistics company

We need a custom, unique , elegant and luxurious full stationary design using our new logo, following these guidelines:
1- Business card: double sided, both sides uses the navy blue as the background main color (same as the code of the navy blue used in our logo).
2- envelope and folder: also use the same navy blue as the main background color.
3- book cover( notepad cover) : same thing with the navy blue
4- letterhead: feel free to use the combination of the colors in our logo.
5- rest of the items are up to your creativity

Target Market(s)

corporates and other businesses

Industry/Entity Type

Logistics and heavy machines contractors

Requirements
Must have
• Letterhead, business card, envelope, notepad cover, paper, file
Nice to have
• navy blue to be main background color for business card, envelope, notepad cover

```html
<!DOCTYPE html>
<html lang="en">
<head>
<meta charset="utf-8">
<title>Northbound Freight Group – Business Card</title>
<link rel="stylesheet" href="https://fonts.googleapis.com/css2?family=Montserrat:wght@400;500;700&display=swap">
<style>
  :root {
    --navy: #0b4470;
    --navy-deep: #083a61;
    --orange: #f0562a;
    --white: #ffffff;
    --sky: #2a9bd8;
    --page: #d9d9d9;
  }
  * { margin: 0; padding: 0; box-sizing: border-box; }
  html, body {
    width: 1200px; height: 800px; overflow: hidden;
    background: var(--page);
    font-family: "Montserrat", sans-serif;
  }
  .canvas {
    position: relative; width: 1200px; height: 800px;
    display: flex; flex-direction: column; align-items: center; justify-content: center; gap: 40px;
  }
  .card {
    position: relative; width: 600px; height: 340px;
    border-radius: 26px;
    background: linear-gradient(160deg, var(--navy) 0%, var(--navy-deep) 100%);
    overflow: hidden;
  }
  /* front side */
  .brand {
    position: absolute; top: 44px; right: 44px;
    display: flex; align-items: center; gap: 10px;
  }
  .brand-dot { width: 14px; height: 14px; border-radius: 50%; background: var(--orange); }
  .brand-name {
    color: var(--white); font-weight: 700; font-size: 17px;
    letter-spacing: 0.04em; text-transform: uppercase;
  }
  .divider {
    position: absolute; left: 60px; right: 40px; top: 190px;
    height: 1px; background: var(--orange);
  }
  .person { position: absolute; left: 60px; top: 128px; }
  .person-name {
    color: var(--orange); font-weight: 700; font-size: 22px;
    text-transform: uppercase; letter-spacing: 0.01em; line-height: 1.1;
  }
  .person-title { color: var(--white); font-size: 15px; font-weight: 500; margin-top: 4px; }
  .contacts { position: absolute; left: 60px; top: 208px; list-style: none; }
  .contacts li {
    display: flex; align-items: center; gap: 10px;
    color: var(--white); font-size: 15px; line-height: 22px;
  }
  .contacts svg { width: 12px; height: 12px; flex: none; }
  .address {
    position: absolute; right: 40px; top: 208px; text-align: right;
    color: var(--white); font-size: 14px; line-height: 21px;
  }
  .address .web { color: var(--orange); letter-spacing: 0.12em; }
  /* back side */
  .card-back { display: flex; align-items: center; justify-content: center; gap: 16px; }
  .card-back .brand-dot { width: 26px; height: 26px; }
  .card-back .brand-name { font-size: 30px; color: var(--sky); }
</style>
</head>
<body>
<main class="canvas">
  <section class="card card-front" aria-label="Business card front">
    <div class="brand">
      <span class="brand-dot"></span>
      <span class="brand-name">Northbound Freight Group</span>
    </div>
    <div class="person">
      <p class="person-name">Daniel Reyes</p>
      <p class="person-title">President</p>
    </div>
    <div class="divider"></div>
    <ul class="contacts">
      <li>
        <svg viewBox="0 0 12 12" aria-hidden="true"><path d="M2.5 1h2l1 3-1.3 1a7 7 0 0 0 2.8 2.8L8 6.5l3 1v2A1.5 1.5 0 0 1 9.5 11 8.5 8.5 0 0 1 1 2.5 1.5 1.5 0 0 1 2.5 1z" fill="#f0562a"/></svg>
        555-014-2387
      </li>
      <li>
        <svg viewBox="0 0 12 12" aria-hidden="true"><rect x="2.5" y="0.8" width="7" height="10.4" rx="1.2" fill="none" stroke="#f0562a" stroke-width="1.4"/></svg>
        555-019-6642
      </li>
      <li>
        <svg viewBox="0 0 12 12" aria-hidden="true"><rect x="0.7" y="2" width="10.6" height="8" rx="1" fill="#f0562a"/><path d="M1 2.5 6 6.5l5-4" fill="none" stroke="#0b4470" stroke-width="1.1"/></svg>
        daniel@nfgfreight.com
      </li>
    </ul>
    <address class="address" style="font-style:normal">
      4120 Harbor View Road<br>
      Fairview, Alaska 99870<br>
      <span class="web">www.nfgfreight.com</span>
    </address>
  </section>

  <section class="card card-back" aria-label="Business card back">
    <span class="brand-dot"></span>
    <span class="brand-name">Northbound Freight Group</span>
  </section>
</main>
</body>
</html>
```